Creative Web Design for an ERP (technology) Consulting Business

I need two pages designed for the ERP Project Management Consulting Company I am starting. One page is the home page, the other page is an important inside page.

I've looked at many different templates for sites like this, and they all look the same to me. I am working with PixelGuild designers because I want something unique.

This site will be implemented with Wordpress using the Elementor framework,

About Me ---
I have worked with PixelGuild several times before, and I have tired to do everything I can to ve helpful. In the uploads, you will find PDF's with wireframes outlning the layout of the pages, as well as explanatios for each section. There are Word documents that you can copy into text. The list below explains the files included.

Although the wireframes suggest a layout, please feel free to use your creativity - often, I find that the designs I like the most are designs I have never thought of.

About the Company --
ERP (Enterprise Resource Planning) systems are business computer systems that tie different businesss functions together. These systems are expensive and complicated, and efforts to implement them often fail. The purpose of the company is to increase the chance of success by focusing on the things that need to be right.

I have uploaded several files to help clarify what I am looking for:
• 1a - Home Page Wireframe - PDF
Wireframe for the home page with an explanation of each section.
• 1b - Home Page Text – Word
A Word document so that you can copy the text.
• 2 - Copper Harbor Logo – ZIP
Four different versions of the company logo in Adobe Illustrator, PNG, and JPG formats. Any of the four are acceptable:
1. Logo_1 – Black on Transparent – Same Line ERP
2. Logo_2 – White on Transparent – Same Line ERP
3. Logo_3 – Black on Transparent – Big ERP on Different Line
4. Logo_4 – White on Transparent – Big ERP on Different Line
• 3a - Copper Harbor Page Wireframe – PDF
Wireframe for he Copper Harbor page, with explanations and a detailed breakdown of the top section.
• 3b - Copper Harbor Text – Word
• 4 - Colors and Palettes – PDF
• 5 - Change Management Icon – EPS
• 6 – Site Map
If you wish to see it, the site map provides an idea of the entire site. The two pages circled in red are the ones I need to be designed.

Thank you for your interest in this project!

Target Market(s)

Corporate decision makers, primarily CIOs and CFOs, as well as ERP project managers and influencers.

Industry/Entity Type

Consulting

Number of Pages Required

2 page

Font styles to use
Sans Serif

Requirements
Must have
• Pages that contain the elements explained on the wireframes provided.
Nice to have
• A design that looks and feels unique
Should not have
• A typical, template layour

```html
<!DOCTYPE html>
<html lang="en">
<head>
<meta charset="utf-8">
<title>Copper Harbor — ERP Consulting</title>
<link href="https://fonts.googleapis.com/css2?family=Inter:wght@400;500;600;700&display=swap" rel="stylesheet">
<style>
  :root {
    --bg: #e5e2f1;
    --ink: #111114;
    --muted: #3b3a44;
    --line: #c7c2db;
    --card: #bcb4da;
    --card-deep: #9d95c8;
    --white: #ffffff;
    --photo-a: #b9aca0;
    --photo-b: #5d5650;
    --video-a: #8b8580;
    --video-b: #2e2c30;
    --accent-red: #d23a3a;
  }
  * { box-sizing: border-box; margin: 0; padding: 0; }
  html, body { width: 673px; height: 1200px; overflow: hidden; }
  body { background: var(--bg); font-family: "Inter", sans-serif; color: var(--ink); position: relative; }

  .site-header { position: absolute; left: 24px; right: 24px; top: 11px; height: 32px; display: flex; align-items: center; }
  .brand { font-weight: 700; font-size: 13px; letter-spacing: -0.2px; }
  .main-nav { display: flex; gap: 26px; margin-left: auto; margin-right: 26px; font-size: 11px; font-weight: 500; }
  .nav-cta { background: var(--ink); color: var(--white); font-size: 10px; font-weight: 600; border-radius: 8px; width: 85px; height: 32px; display: flex; align-items: center; justify-content: center; gap: 12px; }

  .eyebrow { position: absolute; font-size: 11.5px; color: var(--muted); letter-spacing: 0.2px; }

  .hero-title { position: absolute; left: 26px; top: 128px; width: 320px; font-size: 26.5px; line-height: 29px; font-weight: 500; letter-spacing: -0.6px; }
  .hero-text { position: absolute; left: 26px; top: 259px; width: 280px; font-size: 11.5px; line-height: 14px; color: var(--ink); }
  .btn { position: absolute; height: 35px; border-radius: 8px; font-size: 11px; font-weight: 600; display: flex; align-items: center; justify-content: center; }
  .btn-dark { background: var(--ink); color: var(--white); }
  .btn-light { background: var(--white); color: var(--ink); }

  .hero-photo { position: absolute; left: 350px; top: 87px; width: 298px; height: 287px; border-radius: 18px; background: linear-gradient(135deg, var(--photo-a), var(--photo-b)); }

  .divider { position: absolute; left: 26px; right: 24px; top: 428px; height: 1px; background: var(--line); }

  .about-name { position: absolute; left: 24px; top: 516px; font-size: 40px; font-weight: 600; letter-spacing: -1.4px; }
  .about-text { position: absolute; left: 26px; top: 577px; width: 260px; font-size: 10.5px; line-height: 14.5px; color: var(--muted); }

  .profile-card { position: absolute; left: 24px; top: 707px; width: 235px; height: 87px; background: var(--white); border-radius: 10px; }
  .profile-photo { position: absolute; left: 4px; top: 4px; width: 79px; height: 79px; border-radius: 7px; background: linear-gradient(160deg, #8f8a86, #2f3448); }
  .profile-name { position: absolute; left: 94px; top: 22px; font-size: 14px; font-weight: 600; }
  .profile-role { position: absolute; left: 95px; top: 43px; font-size: 9.5px; line-height: 16px; color: #8a8894; }

  .video { position: absolute; left: 348px; top: 446px; width: 300px; height: 164px; border-radius: 12px; overflow: hidden; background: linear-gradient(120deg, var(--video-a), var(--video-b)); }
  .video-label { position: absolute; left: 12px; top: 14px; display: flex; align-items: center; gap: 8px; font-size: 8px; color: var(--white); }
  .video-dot { width: 18px; height: 18px; border-radius: 50%; background: #4a4647; }
  .video-small { position: absolute; left: 12px; top: 128px; font-size: 7px; color: var(--white); }
  .video-controls { position: absolute; left: 0; top: 0; }

  .projects-text { position: absolute; left: 348px; top: 662px; width: 300px; font-size: 17.5px; line-height: 21px; letter-spacing: -0.3px; font-weight: 500; }

  .service-card { position: absolute; top: 842px; width: 199px; height: 312px; border-radius: 16px; background: var(--card); text-align: center; }
  .service-card.featured { background: var(--card-deep); }
  .service-title { position: absolute; left: 10px; right: 10px; top: 52px; font-size: 20.5px; line-height: 25px; font-weight: 500; letter-spacing: -0.4px; }
  .featured .service-title { color: var(--white); }
  .play { position: absolute; left: 50%; top: 140px; width: 32px; height: 32px; margin-left: -16px; border-radius: 50%; background: var(--white); display: flex; align-items: center; justify-content: center; }
  .service-text { position: absolute; left: 16px; right: 16px; top: 195px; font-size: 10.5px; line-height: 14px; color: #4a4760; }
  .featured .service-text { color: var(--white); }
  .service-btn { position: absolute; left: 41px; top: 263px; width: 117px; height: 34px; border-radius: 4px; background: var(--white); font-size: 10px; font-weight: 600; display: flex; align-items: center; justify-content: center; }
  .service-btn.dark { background: var(--ink); color: var(--white); }
</style>
</head>
<body>
  <header class="site-header">
    <div class="brand">COPPER HARBOR</div>
    <nav class="main-nav">
      <span>HOME</span><span>PAGES</span><span>CASES</span><span>ABOUT</span><span>BLOG</span>
    </nav>
    <div class="nav-cta">SIGN UP
      <svg width="8" height="8" viewBox="0 0 8 8"><path d="M0 4h7M4 1l3 3-3 3" stroke="#fff" stroke-width="1.2" fill="none"/></svg>
    </div>
  </header>

  <section class="intro">
    <p class="eyebrow" style="left:26px;top:110px;">INTRODUCTION</p>
    <h1 class="hero-title">Decades in pursuit of excellence in ERP solutions. Let us help you achieve erp success.</h1>
    <p class="hero-text">An honest partner for every step of your ERP journey, from first plan to a system your team trusts.</p>
    <div class="btn btn-dark" style="left:26px;top:313px;width:106px;">GET STARTED</div>
    <div class="btn btn-light" style="left:144px;top:313px;width:99px;">LEARN MORE</div>
    <div class="hero-photo" role="img" aria-label="Photo of consultants working together at a desk"></div>
  </section>

  <div class="divider"></div>

  <section class="about">
    <p class="eyebrow" style="left:26px;top:500px;">ABOUT</p>
    <h2 class="about-name">Henrik Dalby</h2>
    <p class="about-text">Henrik Dalby has led ERP programs for over thirty years. He helps leaders plan, staff and steer projects so that new systems deliver real value, and he knows where efforts fail and how to keep them on track from day one to go-live and beyond.</p>

    <div class="profile-card">
      <div class="profile-photo" role="img" aria-label="Portrait photo of the founder"></div>
      <p class="profile-name">Henrik Dalby ERP</p>
      <p class="profile-role">Founder and lead advisor<br>ERP project expert</p>
    </div>

    <div class="video" role="img" aria-label="Video of the founder introducing the company">
      <div class="video-label"><span class="video-dot"></span>Meet the founder</div>
      <span class="video-small">Intro</span>
      <svg class="video-controls" width="300" height="164" viewBox="0 0 300 164">
        <circle cx="280" cy="17" r="5" fill="none" stroke="#fff" stroke-width="1.4"/>
        <circle cx="20" cy="148" r="5" fill="#fff"/>
        <line x1="30" y1="148" x2="110" y2="148" stroke="var(--accent-red)" stroke-width="2"/>
        <line x1="110" y1="148" x2="232" y2="148" stroke="#bbb" stroke-width="1.5"/>
        <rect x="246" y="143" width="10" height="9" fill="#fff"/>
        <rect x="272" y="142" width="10" height="10" fill="none" stroke="#fff" stroke-width="1.4"/>
      </svg>
    </div>

    <p class="eyebrow" style="left:348px;top:638px;">PROJECTS</p>
    <p class="projects-text">We set up key initiatives and ERP success to help every leader run a better ERP project and command plans.</p>
  </section>

  <section class="services">
    <article class="service-card" style="left:24px;">
      <h3 class="service-title">The ERP Project Management Consultant</h3>
      <div class="play"><svg width="10" height="12" viewBox="0 0 10 12"><path d="M0 0l10 6-10 6z" fill="#111"/></svg></div>
      <p class="service-text">Core client and project plans focused on leading real business results.</p>
      <div class="service-btn">GET STARTED</div>
    </article>
    <article class="service-card featured" style="left:237px;">
      <h3 class="service-title">The Six Pillars and Partner Method</h3>
      <div class="play"><svg width="10" height="12" viewBox="0 0 10 12"><path d="M0 0l10 6-10 6z" fill="#111"/></svg></div>
      <p class="service-text">Key phases of the right path that keep your rollout on budget.</p>
      <div class="service-btn">GET STARTED</div>
    </article>
    <article class="service-card" style="left:450px;">
      <h3 class="service-title">Ready for Everything Consulting</h3>
      <div class="play"><svg width="10" height="12" viewBox="0 0 10 12"><path d="M0 0l10 6-10 6z" fill="#111"/></svg></div>
      <p class="service-text">We help teams stay focused through every change in their business...</p>
      <div class="service-btn dark">GET STARTED</div>
    </article>
  </section>
</body>
</html>
```